BrindleStaffing Business Card Design

We are a staffing company finding positions for dedicated nurses and physicians.

Target Market(s)

Business Professionals

Industry/Entity Type

Staffing

Contact Information for Business Card

Gordon Pratley
Chairman
417 39th Avenue South
SAINT PETERSBURG FL 33712
813-555-4172 Mobile
813-555-8036 Fax
gpratley@brindlestaffing.com
www.brindlestaffing.com

Font styles to use
Sans Serif

Colors
fbee3e
f04a50
f37122

Requirements
Must have
• Logo Attached, see colors below. We'd like to see Yellow, Orange and Red.

```html
<!DOCTYPE html>
<html lang="en">
<head>
<meta charset="utf-8">
<title>BrindleStaffing Business Card</title>
<link href="https://fonts.googleapis.com/css2?family=Open+Sans:wght@400;600;700&family=Oswald:wght@700&display=swap" rel="stylesheet">
<style>
  :root {
    --yellow: #fbee3e;
    --red: #f04a50;
    --orange: #f37122;
    --ink: #1e1e1e;
    --paper: #f6f6f6;
    --backdrop: #222222;
  }
  * { margin: 0; padding: 0; box-sizing: border-box; }
  html, body { width: 1200px; height: 926px; overflow: hidden; background: var(--backdrop); }
  .stage { position: relative; width: 1200px; height: 926px; }
  .card {
    position: absolute;
    width: 560px; height: 320px;
    background: var(--paper);
    border-bottom: 6px solid var(--orange);
    font-family: "Open Sans", sans-serif;
    color: var(--ink);
  }
  .card--front { left: 540px; top: 90px; }
  .card--back { left: 100px; top: 500px; }

  .brand {
    position: absolute; left: 0; right: 0; top: 0; bottom: 0;
    display: flex; align-items: center; justify-content: center; gap: 14px;
  }
  .brand__dot { width: 22px; height: 22px; border-radius: 50%; background: var(--orange); }
  .brand__name { font-weight: 700; font-size: 44px; color: var(--red); letter-spacing: -0.5px; }

  .identity {
    position: absolute; left: 70px; top: 92px; width: 200px; text-align: right;
  }
  .identity__name {
    font-family: "Oswald", sans-serif; font-weight: 700; font-size: 27px;
    line-height: 1.05; color: var(--red); text-transform: uppercase;
  }
  .identity__title { font-size: 15px; margin-top: 2px; }
  .divider { position: absolute; left: 286px; top: 100px; width: 2px; height: 62px; background: var(--ink); }

  .contacts { position: absolute; left: 302px; top: 92px; list-style: none; font-size: 14px; line-height: 19px; }
  .contacts li { display: flex; align-items: center; gap: 7px; }
  .contacts svg { width: 11px; height: 11px; fill: var(--orange); flex: none; }

  .address { position: absolute; left: 40px; bottom: 34px; font-size: 15px; }
</style>
</head>
<body>
<main class="stage">
  <section class="card card--front">
    <div class="brand">
      <span class="brand__dot"></span>
      <span class="brand__name">BrindleStaffing</span>
    </div>
  </section>

  <section class="card card--back">
    <div class="identity">
      <div class="identity__name">Gordon Pratley</div>
      <div class="identity__title">Chairman</div>
    </div>
    <div class="divider"></div>
    <ul class="contacts">
      <li><svg viewBox="0 0 12 12"><path d="M2 0h3l1 3-2 1a7 7 0 0 0 4 4l1-2 3 1v3c0 1-1 2-2 2A10 10 0 0 1 0 2C0 1 1 0 2 0z"/></svg>813-555-4172</li>
      <li><svg viewBox="0 0 12 12"><rect x="3" y="0" width="6" height="4"/><rect x="0" y="4" width="12" height="5" rx="1"/><rect x="3" y="8" width="6" height="4"/></svg>813-555-8036</li>
      <li><svg viewBox="0 0 12 12"><path d="M0 2h12v8H0z M0 2l6 5 6-5" /></svg>gpratley@brindlestaffing.com</li>
      <li><svg viewBox="0 0 12 12"><circle cx="6" cy="6" r="6"/></svg>www.brindlestaffing.com</li>
    </ul>
    <p class="address">417 39th Avenue South, SAINT PETERSBURG FL 33712</p>
  </section>
</main>
</body>
</html>
```